Harborline Renewal Business Card Design

Professional and clean design. The design colors should flow with the logo. Two-sided card with the website on the back which is:

www.HarborlineRenewal.example.

"Specializing in Water Damage Restoration"

On the front I need the name, email, phone, and logo.

Name: Darnell Quisby
Email: Darnell@HarborlineRenewal.example
Phone: 555-318-2046 for now

I only have the Preview and Thumbnail right now but should have the source files uploaded within a day or two.

Target Market(s)

Flood victims, home owners with water damage from busted pipes etc...

Industry/Entity Type

Business

Contact Information for Business Card

Name: Darnell Quisby

Font styles to use
Serif
Sans Serif

Requirements
Must have
• Business Card Details Info

```html
<!DOCTYPE html>
<html lang="en">
<head>
<meta charset="utf-8">
<title>Harborline Renewal Business Card</title>
<link rel="stylesheet" href="https://fonts.googleapis.com/css2?family=Cinzel:wght@400;500&family=Open+Sans:wght@400&display=swap">
<style>
  :root {
    --backdrop: #eeeeec;
    --card: #050505;
    --brand-blue: #2a8fd2;
    --wave-light: #56c3f0;
    --wave-deep: #2a8fd2;
    --text-light: #f2f2f2;
    --rule: #5a5a5a;
  }
  * { margin: 0; padding: 0; box-sizing: border-box; }
  html, body {
    width: 1200px; height: 1188px; overflow: hidden;
    background: var(--backdrop);
  }
  .canvas { position: relative; width: 1200px; height: 1188px; }
  .card {
    position: absolute; width: 909px; height: 520px;
    background: var(--card); border-radius: 38px; overflow: hidden;
  }
  .card--front { left: 51px; top: 70px; }
  .card--back { left: 221px; top: 631px; }

  .brand-mark {
    position: absolute; border-radius: 50%; background: var(--brand-blue);
  }
  .brand-name {
    position: absolute; font-family: "Cinzel", serif; font-weight: 500;
    color: var(--brand-blue); text-align: center; text-transform: uppercase;
    line-height: 1.05; letter-spacing: 0.02em;
  }
  .card--front .brand-mark { left: 170px; top: 133px; width: 108px; height: 108px; }
  .card--front .brand-name { left: 10px; width: 428px; top: 258px; font-size: 44px; }

  .divider {
    position: absolute; left: 431px; top: 144px; width: 2px; height: 199px;
    background: var(--rule);
  }
  .person { position: absolute; left: 458px; top: 146px; }
  .person-name {
    font-family: "Cinzel", serif; font-size: 31px; color: var(--brand-blue);
    letter-spacing: 0.03em; line-height: 1.1;
  }
  .person-title {
    font-family: "Cinzel", serif; font-size: 26px; color: var(--text-light);
    letter-spacing: 0.12em; margin-top: 4px;
  }
  .contact-list { list-style: none; margin-top: 30px; }
  .contact-list li {
    display: flex; align-items: center; gap: 12px;
    font-family: "Open Sans", sans-serif; font-size: 21px; color: var(--text-light);
    height: 36px;
  }
  .contact-list svg { width: 18px; height: 18px; flex: none; }

  .waves { position: absolute; left: 0; bottom: 0; width: 909px; height: 140px; }

  .card--back .brand-mark { left: 369px; top: 60px; width: 170px; height: 170px; }
  .card--back .brand-name { left: 0; width: 909px; top: 262px; font-size: 60px; }
  .tagline {
    position: absolute; left: 0; width: 909px; top: 440px; text-align: center;
    font-family: "Cinzel", serif; font-size: 26px; color: var(--brand-blue);
    letter-spacing: 0.02em;
  }
</style>
</head>
<body>
<main class="canvas">
  <section class="card card--front" aria-label="Card front">
    <div class="brand-mark" aria-hidden="true"></div>
    <div class="brand-name">Harborline<br>Renewal</div>
    <div class="divider"></div>
    <div class="person">
      <p class="person-name">Darnell Quisby</p>
      <p class="person-title">Title</p>
      <ul class="contact-list">
        <li>
          <svg viewBox="0 0 20 20" aria-hidden="true"><path d="M5 2.5c1 0 2.5 3.2 2.5 4 0 .8-1.3 1.3-1.3 2 0 1.4 3.6 5 5 5 .7 0 1.2-1.3 2-1.3.8 0 4 1.5 4 2.5 0 1.8-2 3-3.5 3C7.8 17.7 2.3 12.2 2.3 6.3 2.3 4.6 3.4 2.5 5 2.5z" fill="none" stroke="#f2f2f2" stroke-width="1.6"/></svg>
          555-318-2046
        </li>
        <li>
          <svg viewBox="0 0 20 20" aria-hidden="true"><rect x="1.5" y="4" width="17" height="12" rx="1.5" fill="#f2f2f2"/><path d="M2 5l8 6 8-6" fill="none" stroke="#050505" stroke-width="1.6"/></svg>
          Darnell@HarborlineRenewal.example
        </li>
        <li>
          <svg viewBox="0 0 20 20" aria-hidden="true"><g fill="none" stroke="#f2f2f2" stroke-width="1.4"><circle cx="10" cy="10" r="8"/><ellipse cx="10" cy="10" rx="3.5" ry="8"/><path d="M2 10h16M3.5 5.5h13M3.5 14.5h13"/></g></svg>
          www.HarborlineRenewal.example
        </li>
      </ul>
    </div>
    <svg class="waves" viewBox="0 0 909 140" preserveAspectRatio="none" aria-hidden="true">
      <path d="M0 52 C220 30 470 62 650 40 C770 26 860 8 909 0 L909 140 L0 140 Z" fill="var(--wave-light)"/>
      <path d="M300 28 C480 48 600 62 740 66" fill="none" stroke="#050505" stroke-width="5"/>
      <path d="M0 104 C260 74 560 104 909 30 L909 140 L0 140 Z" fill="#050505"/>
      <path d="M0 114 C280 86 580 114 909 44 L909 140 L0 140 Z" fill="var(--wave-deep)"/>
    </svg>
  </section>

  <section class="card card--back" aria-label="Card back">
    <div class="brand-mark" aria-hidden="true"></div>
    <div class="brand-name">Harborline Renewal</div>
    <p class="tagline">Specializing in Water Damage Restoration</p>
  </section>
</main>
</body>
</html>
```